Irrigation Business needs their business cards modernised and revamped

I would like to keep my current logo, colours and revamp the format of the card.

I would like the card to be clean yet important.

Im not sure if you include texture but i would like the named logo to be indented into the card etc.

show me something alive and free something thats clinical to the point yet has a feel of achievement. i would like people to go nice card.

Target Market(s)

high end clients, corporate, sports field manger, the guys that make the decisions

Industry/Entity Type

Business

Contact Information for Business Card

nformation to be included

Dean Harlow (Director)
0487305526
dean@kolvat.biz
www.kestonfieldworks.com

instagram logo
google logo
facebook logo

Colors

Designer to choose colors to be used in the design.

Requirements
Nice to have
• indentations a really nice feel to the card good texture

```html
<!DOCTYPE html>
<html lang="en">
<head>
<meta charset="utf-8">
<title>Keston Fieldworks – Business Card</title>
<link rel="stylesheet" href="https://fonts.googleapis.com/css2?family=Open+Sans:wght@400;600;700;800&display=swap">
<style>
  :root {
    --stage: #2b2b2d;
    --paper: #ffffff;
    --brand-blue: #2f6dbf;
    --deep-blue: #1d55aa;
    --sky-blue: #34a9dc;
    --leaf-green: #3fae4a;
    --ink-white: #ffffff;
  }
  * { box-sizing: border-box; margin: 0; padding: 0; }
  html, body {
    width: 1200px; height: 840px; overflow: hidden;
    background: var(--stage);
    font-family: "Open Sans", Arial, sans-serif;
  }
  .canvas {
    width: 1200px; height: 840px;
    display: flex; align-items: center; justify-content: center; gap: 40px;
  }
  .card {
    position: relative;
    width: 540px; height: 300px;
    background: var(--paper);
    overflow: hidden;
    box-shadow: 0 10px 30px rgba(0,0,0,.35);
  }

  /* Front */
  .card--front {
    display: flex; flex-direction: column; align-items: center; justify-content: center;
  }
  .brand-dot {
    width: 78px; height: 78px; border-radius: 50%;
    background: var(--sky-blue);
    margin-bottom: 14px;
  }
  .brand-name {
    color: var(--brand-blue);
    font-weight: 800;
    font-size: 30px;
    letter-spacing: .5px;
    text-transform: uppercase;
    line-height: 1;
  }
  .social-row { display: flex; gap: 8px; margin-top: 16px; }
  .social-dot {
    width: 16px; height: 16px; border-radius: 50%;
    background: var(--brand-blue);
  }

  /* Back */
  .card__art { position: absolute; inset: 0; }
  .person {
    position: absolute; left: 40px; top: 130px;
    text-transform: uppercase; line-height: 1.25;
  }
  .person__name { color: var(--brand-blue); font-weight: 700; font-size: 15px; }
  .person__role { color: var(--leaf-green); font-weight: 600; font-size: 14px; }
  .contacts {
    position: absolute; left: 90px; bottom: 22px;
    list-style: none; color: var(--ink-white); font-size: 14px; line-height: 1.45;
  }
  .contacts li { display: flex; align-items: center; gap: 8px; }
  .contacts svg { width: 12px; height: 12px; flex: none; }
</style>
</head>
<body>
<main class="canvas">

  <section class="card card--front" aria-label="Card front">
    <div class="brand-dot"></div>
    <h1 class="brand-name">Keston Fieldworks</h1>
    <div class="social-row" aria-label="Social media">
      <span class="social-dot"></span>
      <span class="social-dot"></span>
      <span class="social-dot"></span>
    </div>
  </section>

  <section class="card card--back" aria-label="Card back">
    <svg class="card__art" viewBox="0 0 540 300" aria-hidden="true">
      <defs>
        <linearGradient id="bandFill" x1="0" y1="1" x2="1" y2="0">
          <stop offset="0" stop-color="#1d55aa"/>
          <stop offset="1" stop-color="#2468c4"/>
        </linearGradient>
      </defs>
      <polygon points="0,218 540,120 540,300 0,300" fill="url(#bandFill)"/>
      <circle cx="405" cy="118" r="112" fill="#34a9dc" stroke="#ffffff" stroke-width="7"/>
    </svg>

    <div class="person">
      <div class="person__name">Dean Harlow</div>
      <div class="person__role">Director</div>
    </div>

    <ul class="contacts">
      <li>
        <svg viewBox="0 0 12 12"><path fill="#fff" d="M2.5 1l2 2-1 1.2a7 7 0 0 0 3.8 3.8L8.5 7l2 2-1.3 1.5C5 10.5 1.5 7 1 2.8z"/></svg>
        0487305526
      </li>
      <li>
        <svg viewBox="0 0 12 12"><rect x="1" y="2.5" width="10" height="7" rx="1" fill="#fff"/><path d="M1.5 3l4.5 3.5L10.5 3" stroke="#1d55aa" stroke-width="1" fill="none"/></svg>
        dean@kolvat.biz
      </li>
      <li>
        <svg viewBox="0 0 12 12"><circle cx="6" cy="6" r="5" fill="#fff"/><path d="M1 6h10M6 1c-2 2.5-2 7.5 0 10M6 1c2 2.5 2 7.5 0 10" stroke="#1d55aa" stroke-width=".8" fill="none"/></svg>
        www.kestonfieldworks.com
      </li>
    </ul>
  </section>

</main>
</body>
</html>
```